Business Card Design 2018 Kestrel Machining

Hello,

We need a business card design to reflect our new website we just had designed ( http://www.kestrelmachining.ca/)

We are a growing machine shop looking to grow our clientele and are hoping to update our current business card design to match our website and industry

The colours and design of our website should match to achieve what we are looking for.

I have attached a few images for reference as well as our logo and ISO 9000 needs to be apparent on the card as well

Please let me know what you have :)
Please copy marla@kestrelmachining.ca on all communication regarding this project

Thanks !!!

Industry/Entity Type

Business

Contact Information for Business Card

Company Name, employee name and title and contact details

Colors
f78f20
ffffff
00a990

Requirements
Must have
• Our logo, Iso 9000 same colours as our website http://www.kestrelmachining.ca/

```html
<!DOCTYPE html>
<html lang="en">
<head>
<meta charset="utf-8">
<title>Kestrel Machining Business Card</title>
<link href="https://fonts.googleapis.com/css2?family=Roboto+Condensed:wght@400;700&display=swap" rel="stylesheet">
<style>
  :root {
    --bg: #e9e6e1;
    --card-light: #fbfbfa;
    --card-dark: #0b0b0b;
    --teal: #2fb4c2;
    --ink: #1a1a1a;
    --muted: #5e5e5e;
    --rule: #8a8a8a;
    --white: #ffffff;
  }
  * { margin: 0; padding: 0; box-sizing: border-box; }
  html, body { width: 1200px; height: 886px; overflow: hidden; }
  body {
    background: var(--bg);
    font-family: "Roboto Condensed", "Arial Narrow", sans-serif;
    position: relative;
  }
  .card {
    position: absolute;
    top: 288px;
    width: 540px;
    height: 309px;
    box-shadow: 0 10px 28px rgba(0,0,0,0.25);
  }
  .card--front { left: 40px; background: var(--card-light); }
  .card--back { left: 620px; background: var(--card-dark); }

  .brand {
    position: absolute;
    display: flex;
    align-items: center;
    gap: 12px;
  }
  .brand__mark { width: 34px; height: 34px; background: var(--teal); flex: none; }
  .brand__name {
    font-weight: 700;
    font-size: 34px;
    letter-spacing: 1px;
    text-transform: uppercase;
    line-height: 1;
  }
  .card--front .brand { left: 130px; top: 64px; }
  .card--front .brand__name { color: var(--ink); }
  .card--back .brand { left: 50%; top: 50%; transform: translate(-50%, -50%); }
  .card--back .brand__name { color: var(--white); }

  .divider {
    position: absolute;
    left: 34px; right: 34px; top: 178px;
    height: 1px;
    background: var(--rule);
  }
  .person { position: absolute; left: 34px; top: 192px; }
  .person__name { color: var(--teal); font-weight: 700; font-size: 19px; text-transform: uppercase; }
  .person__title { color: var(--ink); font-size: 15px; text-transform: uppercase; margin-top: 2px; }
  .person__address { color: var(--muted); font-size: 14px; margin-top: 4px; line-height: 1.3; }

  .contact {
    position: absolute;
    right: 34px; top: 192px;
    list-style: none;
    text-align: right;
    color: var(--muted);
    font-size: 14px;
    line-height: 1.45;
  }
  .contact li { display: flex; justify-content: flex-end; align-items: center; gap: 7px; }
  .contact svg { width: 12px; height: 12px; flex: none; }

  .web {
    position: absolute;
    left: 30px; bottom: 26px;
    color: var(--white);
    font-size: 12px;
    letter-spacing: 3px;
  }
  .badges { position: absolute; right: 26px; bottom: 22px; display: flex; gap: 14px; align-items: center; }
  .badge--cert { width: 48px; height: 22px; border: 2px solid var(--white); }
  .badge--listing { width: 40px; height: 22px; background: var(--white); }
</style>
</head>
<body>

<section class="card card--front" aria-label="Business card front">
  <div class="brand">
    <span class="brand__mark"></span>
    <span class="brand__name">Kestrel Machining</span>
  </div>
  <div class="divider"></div>
  <div class="person">
    <p class="person__name">Owen Hale</p>
    <p class="person__title">CEO/Founder</p>
    <p class="person__address">214 Birchwood Road<br>Halifax, Nova Scotia B3K 2L9</p>
  </div>
  <ul class="contact">
    <li>902 555 0172
      <svg viewBox="0 0 12 12"><path d="M3 1 L5 3.5 L4 5 Q5 7 7 8 L8.5 7 L11 9 L9.5 11 Q4 10.5 1 3 Z" fill="var(--teal)"/></svg></li>
    <li>902 555 0148
      <svg viewBox="0 0 12 12"><rect x="3" y="1" width="6" height="10" rx="1" fill="none" stroke="var(--teal)" stroke-width="1.4"/></svg></li>
    <li>902 555 0193
      <svg viewBox="0 0 12 12"><rect x="1" y="4" width="10" height="6" fill="var(--teal)"/><rect x="3" y="1" width="6" height="3" fill="var(--teal)"/></svg></li>
    <li>marla@kestrelmachining.ca
      <svg viewBox="0 0 12 12"><rect x="0.5" y="2" width="11" height="8" fill="var(--teal)"/><path d="M1 2.5 L6 6.5 L11 2.5" fill="none" stroke="var(--white)" stroke-width="1"/></svg></li>
  </ul>
</section>

<section class="card card--back" aria-label="Business card back">
  <div class="brand">
    <span class="brand__mark"></span>
    <span class="brand__name">Kestrel Machining</span>
  </div>
  <p class="web">www.kestrelmachining.ca</p>
  <div class="badges">
    <span class="badge--cert" role="img" aria-label="Quality certification badge"></span>
    <span class="badge--listing" role="img" aria-label="Supplier listing badge"></span>
  </div>
</section>

</body>
</html>
```